Business card for event manager / organizer "waiter service"

Draft of a new valuable business card for my company.
Events, personnel service providers, festivals

```html
<!DOCTYPE html>
<html lang="de">
<head>
<meta charset="utf-8">
<title>Jonas Kellnerservice – Visitenkarte</title>
<link href="https://fonts.googleapis.com/css2?family=Arimo:wght@400;700&family=Quicksand:wght@400&display=swap" rel="stylesheet">
<style>
  :root{
    --bg:#ededed;
    --card:#333333;
    --orange:#e8731c;
    --orange-dark:#7a3508;
    --white:#ffffff;
    --muted:#d9d9d9;
    --photo-top:#2a2a2a;
    --photo-mid:#1c202a;
  }
  *{margin:0;padding:0;box-sizing:border-box}
  html,body{width:1200px;height:802px;overflow:hidden;background:var(--bg)}
  body{position:relative;font-family:"Arimo",Arial,sans-serif}
  .card{position:absolute;top:233px;width:520px;height:336px;background:var(--card);overflow:hidden;box-shadow:0 6px 18px rgba(0,0,0,.18)}
  .card--front{left:60px}
  .card--back{left:620px}

  /* front */
  .portrait{position:absolute;left:0;bottom:0;width:250px;height:260px;
    background:linear-gradient(180deg,var(--photo-top) 0%,var(--photo-mid) 60%,var(--photo-mid) 100%)}
  .brand{position:absolute;display:flex;align-items:center;gap:10px}
  .brand__mark{width:28px;height:28px;background:var(--orange);flex:none}
  .brand__name{color:var(--white);font-weight:700;letter-spacing:.5px;line-height:1;white-space:nowrap}
  .brand__tag{font-family:"Quicksand",sans-serif;color:var(--muted);margin-top:4px;white-space:nowrap}
  .card--front .brand{top:26px;right:28px}
  .card--front .brand__name{font-size:20px}
  .card--front .brand__tag{font-size:8px}

  .person{position:absolute;right:28px;top:96px;text-align:right}
  .person__name{color:var(--orange);font-weight:700;font-size:22px}
  .person__role{color:var(--white);font-size:13px;margin-top:3px}

  .contacts{position:absolute;right:28px;top:156px;list-style:none}
  .contacts li{display:flex;justify-content:flex-end;align-items:center;gap:8px;color:var(--white);font-size:13px;height:19px;white-space:nowrap}
  .contacts svg{width:12px;height:12px;flex:none}

  .address-band{position:absolute;right:0;bottom:0;width:300px;height:38px;
    background:linear-gradient(90deg,var(--orange),var(--orange-dark));
    color:var(--white);font-size:13.5px;display:flex;align-items:center;padding-left:22px;white-space:nowrap}

  /* back */
  .card--back .brand{left:50%;top:50%;transform:translate(-50%,-50%);gap:16px}
  .card--back .brand__mark{width:56px;height:56px}
  .card--back .brand__name{font-size:28px}
  .card--back .brand__tag{font-size:12px;margin-top:8px}
</style>
</head>
<body>

<section class="card card--front" aria-label="Vorderseite">
  <div class="portrait" role="img" aria-label="Porträtfoto des Inhabers in dunklem Hemd"></div>

  <div class="brand">
    <div class="brand__mark"></div>
    <div>
      <div class="brand__name">JONAS KELLNERSERVICE</div>
      <div class="brand__tag">...wir servieren, Sie feiern entspannt!</div>
    </div>
  </div>

  <div class="person">
    <div class="person__name">Jonas Brenneke</div>
    <div class="person__role">Inhaber</div>
  </div>

  <ul class="contacts">
    <li>02361 555 01 23
      <svg viewBox="0 0 12 12"><circle cx="6" cy="6" r="6" fill="var(--orange)"/><path d="M3.5 3.2c.4-.4.9-.3 1.1.1l.5 1c.1.3 0 .5-.2.7l-.3.3c.4.8 1 1.4 1.8 1.8l.3-.3c.2-.2.5-.3.7-.2l1 .5c.4.2.5.7.1 1.1-.6.6-1.5.7-2.3.2C4.7 7.7 4.3 7.3 3.6 5.9c-.5-.9-.4-2-.1-2.7z" fill="var(--white)"/></svg></li>
    <li>0170 555 48 21
      <svg viewBox="0 0 12 12"><circle cx="6" cy="6" r="6" fill="var(--orange)"/><rect x="4.2" y="2.6" width="3.6" height="6.8" rx=".6" fill="var(--white)"/></svg></li>
    <li>info@jonas-kellnerservice.de
      <svg viewBox="0 0 12 12"><rect x="0" y="2" width="12" height="8" rx="1" fill="var(--orange)"/><path d="M.5 2.5 6 6.5l5.5-4" fill="none" stroke="var(--white)" stroke-width="1"/></svg></li>
    <li>www.jonas-kellnerservice.de
      <svg viewBox="0 0 12 12"><circle cx="6" cy="6" r="5.5" fill="var(--orange)"/><ellipse cx="6" cy="6" rx="2.3" ry="5" fill="none" stroke="var(--white)" stroke-width=".8"/><path d="M1 6h10" stroke="var(--white)" stroke-width=".8"/></svg></li>
    <li>jonaskellnerservice
      <svg viewBox="0 0 12 12"><circle cx="6" cy="6" r="6" fill="var(--orange)"/></svg></li>
  </ul>

  <div class="address-band">Lindenstraße 14, 45699 Feldhausen</div>
</section>

<section class="card card--back" aria-label="Rückseite">
  <div class="brand">
    <div class="brand__mark"></div>
    <div>
      <div class="brand__name">JONAS KELLNERSERVICE</div>
      <div class="brand__tag">...wir servieren, Sie feiern entspannt!</div>
    </div>
  </div>
</section>

</body>
</html>
```